Business card

We need a business card design for our company based in Auckland , New Zealand called 'Ridge + Studio Ltd'. We provide architectural services. We would like to see designs that use the max. three colours (such as white, black, grey) The final design should communicate financial safety and growth."
Also I will provide our company logo. I would like to the logo to be embeded onto our business card.

Target Market(s)

new residential house, alteration & addition & light commericila design & drafting service

Industry/Entity Type

Architecture

Contact Information for Business Card

Company name: ridge + studio Ltd.
Name: Mark Delford
Job title: architectural designer & Design LBP
email address: mark@rplusd.co.nz
mobile number: 02 5163 2290
web site: www.rplusd.co.nz

Requirements
Must have
• My project must have..
• - embeded logo (attached company logo)
• I don't have a bigger version for our company logo, but I have one old one, so you can remove the word from it)
• - insert the attached small BKTW logo & LBP logo
• - creative, simple and clear business card.
• - Max. three colours
Nice to have
• - Here are the samples I would like to share with you: http://www.plimvora.com/blog/minimalistic-business-card-designs/
• I would like to have my business card like one of the creation.
Should not have
• TBA

```html
<!DOCTYPE html>
<html lang="en">
<head>
<meta charset="utf-8">
<title>Ridge + Studio Ltd — Business Card</title>
<link rel="stylesheet" href="https://fonts.googleapis.com/css2?family=Open+Sans:wght@400;600;700&display=swap">
<style>
  :root {
    --backdrop: #3f3f3f;
    --paper: #ffffff;
    --ink: #111111;
    --muted: #8a8f8c;
    --reverse: #000000;
    --reverse-ink: #ffffff;
  }
  * { box-sizing: border-box; margin: 0; padding: 0; }
  html, body {
    width: 1105px;
    height: 1200px;
    overflow: hidden;
    background: var(--backdrop);
    font-family: "Open Sans", Arial, sans-serif;
  }
  .card {
    position: absolute;
    left: 212px;
    width: 681px;
    height: 410px;
  }
  .card--front { top: 150px; background: var(--paper); color: var(--ink); }
  .card--back { top: 640px; background: var(--reverse); color: var(--reverse-ink); }

  .accent-bar {
    position: absolute; left: 0; top: 119px;
    width: 14px; height: 52px; background: var(--ink);
  }
  .holder-name {
    position: absolute; left: 47px; top: 116px;
    font-size: 24px; font-weight: 600; letter-spacing: 0.3px;
  }
  .holder-title {
    position: absolute; left: 47px; top: 150px;
    font-size: 17px; color: var(--muted);
  }
  .rule {
    position: absolute; left: 48px; top: 203px;
    width: 384px; height: 2px; background: var(--ink);
  }
  .company-name {
    position: absolute; left: 47px; top: 240px;
    font-size: 18px;
  }
  .contact-list {
    position: absolute; left: 47px; top: 282px;
    list-style: none;
  }
  .contact-list li {
    display: flex; align-items: center; gap: 10px;
    height: 28px; font-size: 18px;
  }
  .contact-list svg { width: 17px; height: 17px; flex: none; }

  .brand-mark {
    position: absolute; left: 431px; top: 85px;
    width: 242px; height: 242px;
    display: flex; align-items: center; justify-content: center;
  }
  .brand-mark svg { position: absolute; inset: 0; }
  .brand-name {
    position: relative; font-size: 22px; font-weight: 600; color: var(--ink);
  }

  .partner-badge {
    position: absolute; left: 112px; top: 86px;
    width: 182px; height: 182px;
  }
  .divider {
    position: absolute; left: 324px; top: 95px;
    width: 2px; height: 221px;
    background: linear-gradient(to bottom, rgba(255,255,255,0), #fff 30%, #fff 70%, rgba(255,255,255,0));
  }
  .partner-name {
    position: absolute; left: 350px; top: 128px;
    font-size: 72px; font-weight: 700; line-height: 1; letter-spacing: -1px;
  }
  .back-url {
    position: absolute; left: 0; right: 0; top: 346px;
    text-align: center; font-size: 19px;
  }
</style>
</head>
<body>
  <section class="card card--front">
    <div class="accent-bar"></div>
    <h1 class="holder-name">MARK DELFORD</h1>
    <p class="holder-title">architectural designer &amp; Design LBP</p>
    <div class="rule"></div>
    <p class="company-name">Ridge + Studio Ltd.</p>
    <ul class="contact-list">
      <li>
        <svg viewBox="0 0 16 16"><rect x="4" y="1" width="8" height="14" rx="1.5" fill="none" stroke="#111" stroke-width="1.8"/><rect x="6.5" y="12" width="3" height="1.2" fill="#111"/></svg>
        02 5163 2290
      </li>
      <li>
        <svg viewBox="0 0 16 16"><rect x="1" y="4" width="14" height="9" fill="#111"/><path d="M1 4 L8 9 L15 4" fill="none" stroke="#fff" stroke-width="1.2"/></svg>
        mark@rplusd.co.nz
      </li>
      <li>
        <svg viewBox="0 0 16 16"><circle cx="8" cy="8" r="7" fill="#111"/><path d="M4 6 Q7 4 8 7 T12 10" fill="none" stroke="#fff" stroke-width="1.3"/></svg>
        www.rplusd.co.nz
      </li>
    </ul>
    <div class="brand-mark">
      <svg viewBox="0 0 242 242"><circle cx="121" cy="121" r="116" fill="none" stroke="#111" stroke-width="6"/></svg>
      <span class="brand-name">Ridge + Studio</span>
    </div>
  </section>

  <section class="card card--back">
    <svg class="partner-badge" viewBox="0 0 182 182"><circle cx="91" cy="91" r="90" fill="#fff"/></svg>
    <div class="divider"></div>
    <p class="partner-name">BKTW</p>
    <p class="back-url">www.rplusd.co.nz</p>
  </section>
</body>
</html>
```